Company or website name
- Velmira, LLC
- Velmira, LLC
- Describe your company and organization and target audience
- Velmira, LLC is a research, science and technology based manufacturing company that formulates, develops, manufactures and packages a full complement of personal care products for domestic and international concerns. We private label and contract package personal care products, cosmetics, bath salts and powders and home fragrance products. Velmira is conveniently located in Southern California adjacent to major transportation hubs and international airports. We utilize earth friendly, green manufacturing processes, maximize the use of renewable resource raw materials and minimize the use of non-renewable and petrochemical based raw materials. We provide formulation and product development services with low minimum order quantities and short lead times. Velmira is the intersection between nature, science, beauty and innovation. We are a B-2-B company.
- The design should have the following
- We're looking for an ad design that can be used for both banner and column use online and in print. We manufacture bath and body products such as bath salts, body washes, body powders, bath oils and bubble baths, hair care products such as shampoos, conditioners and styling aids, skin care products such as anti-aging creams, cleansers, masks, toners and serums, color cosmetics such as eyeliners, mascaras, foundations and mineral make-up powders, manicure/pedicure products such as cuticle oils, sugar and salt scrubs and foot soaks/softeners and spa products such as seaweed wraps, cellulite creams, body masks, massage oils and candles. Our strengths are natural and organic product formulation, low minimums, competitive prices, complete research &development services new and innovative ingredients and fast turnaround times. Examples can be found at the following sites: http://www.glintor.com/ http://www.grovewellboard.org/ http://www.tessaloomjournal.com/ http://nerwast.org/images/downloads/bulletins/2009-10-bulletin.pdf http://www.pantrykestrelworks.com/

```html
<!DOCTYPE html>
<html lang="en">
<head>
<meta charset="utf-8">
<title>Velmira, LLC</title>
<link rel="stylesheet" href="https://fonts.googleapis.com/css2?family=Montserrat:wght@300;400&family=Arimo:wght@400&display=swap">
<style>
  :root {
    --green: #5f9a34;
    --green-dark: #4b7e2a;
    --nav-active: #1f5e12;
    --orange-start: #ff6000;
    --orange-end: #ffa514;
    --pill-text: #eef2ea;
    --address: #6e6257;
    --white: #ffffff;
  }
  * { box-sizing: border-box; margin: 0; padding: 0; }
  html, body { width: 1146px; height: 1200px; overflow: hidden; background: var(--white); }
  .canvas { position: relative; width: 1146px; height: 1200px; background: var(--white); font-family: "Montserrat", sans-serif; }
  .edge { position: absolute; top: 0; bottom: 0; background: var(--green); }
  .edge-left { left: 0; width: 11px; }
  .edge-right { right: 0; width: 18px; }

  .brand { position: absolute; left: 40px; top: 30px; height: 100px; display: flex; align-items: center; gap: 18px; }
  .brand-dot { width: 44px; height: 44px; border-radius: 50%; background: var(--green); }
  .brand-name { font-weight: 300; font-size: 72px; line-height: 1; color: var(--green); letter-spacing: 1px; }

  .address { position: absolute; right: 35px; top: 30px; text-align: right; font-family: "Arimo", sans-serif; font-size: 15.5px; line-height: 21px; color: var(--address); font-style: normal; }

  .nav { position: absolute; left: 24px; top: 172px; width: 203px; height: 319px; background: var(--green); list-style: none; font-family: "Arimo", sans-serif; font-size: 14.5px; }
  .nav li { position: absolute; left: 8px; color: var(--white); }
  .nav li.active { color: var(--nav-active); }

  .strengths { position: absolute; left: 24px; top: 517px; width: 477px; }
  .strengths-title { height: 72px; background: linear-gradient(90deg, var(--orange-start), var(--orange-end)); color: var(--white); font-weight: 300; font-size: 44px; line-height: 72px; text-align: center; letter-spacing: 1px; }
  .strengths-list { background: var(--green); height: 146px; padding: 6px 0 0 8px; list-style: none; color: var(--white); font-weight: 300; font-size: 20.5px; line-height: 27.5px; white-space: nowrap; }

  .panel { position: absolute; left: 511px; width: 605px; }
  .panel-body { position: absolute; left: 0; right: 0; top: 25px; bottom: 0; background: var(--green); border-bottom-right-radius: 14px; }
  .panel-tab { position: absolute; left: 0; top: 0; height: 50px; padding-left: 17px; background: linear-gradient(90deg, var(--orange-start), var(--orange-end)); clip-path: polygon(0 0, calc(100% - 24px) 0, 100% 50%, calc(100% - 24px) 100%, 0 100%); color: var(--white); font-weight: 300; font-size: 29px; line-height: 50px; letter-spacing: 0.5px; white-space: nowrap; }
  .pill { position: absolute; width: 189px; height: 39px; background: var(--green-dark); clip-path: polygon(0 0, calc(100% - 15px) 0, 100% 50%, calc(100% - 15px) 100%, 0 100%); color: var(--pill-text); font-weight: 300; font-size: 21px; line-height: 39px; text-align: center; letter-spacing: 0.5px; white-space: nowrap; }
  .pill.wide { width: 387px; }
  .c1 { left: 8px; } .c2 { left: 206px; } .c3 { left: 404px; }
  .r1 { top: 61px; } .r2 { top: 112px; }
</style>
</head>
<body>
<div class="canvas">
  <div class="edge edge-left"></div>
  <div class="edge edge-right"></div>

  <header class="brand">
    <span class="brand-dot"></span>
    <span class="brand-name">Velmira</span>
  </header>

  <address class="address">
    4120 E. Larkspur Avenue<br>
    Building 20<br>
    Fullerton, CA 92831<br>
    714.555.0141 P<br>
    714.555.0142 F<br>
    info@velmira.com
  </address>

  <ul class="nav">
    <li class="active" style="top:19px">Home</li>
    <li style="top:66px">Product Development</li>
    <li style="top:113px">Manufacturing</li>
    <li style="top:165px">Filling and Packaging</li>
    <li style="top:221px">Resources</li>
    <li style="top:273px">Contact Us</li>
  </ul>

  <section class="strengths">
    <h2 class="strengths-title">Our strengths are</h2>
    <ul class="strengths-list">
      <li>natural and organic product formulation</li>
      <li>low minimums , competitive prices</li>
      <li>complete research &amp; development services</li>
      <li>new and innovative ingredients</li>
      <li>and fast turnaround times</li>
    </ul>
  </section>

  <section class="panel" style="top:172px;height:167px">
    <div class="panel-body"></div>
    <h3 class="panel-tab" style="width:423px">bath and body products</h3>
    <span class="pill c1 r1">bath salt</span>
    <span class="pill c2 r1">body wash</span>
    <span class="pill c3 r1">body powder</span>
    <span class="pill c1 r2">bath oil</span>
    <span class="pill c2 r2">bubble bath</span>
  </section>

  <section class="panel" style="top:352px;height:116px">
    <div class="panel-body"></div>
    <h3 class="panel-tab" style="width:355px">hair care products</h3>
    <span class="pill c1 r1">shampoo</span>
    <span class="pill c2 r1">conditioners</span>
    <span class="pill c3 r1">styling aid</span>
  </section>

  <section class="panel" style="top:481px;height:166px">
    <div class="panel-body"></div>
    <h3 class="panel-tab" style="width:355px">skin care products</h3>
    <span class="pill wide c1 r1">anti - aging cream</span>
    <span class="pill c3 r1">cleanser</span>
    <span class="pill c1 r2">mask</span>
    <span class="pill c2 r2">toner</span>
    <span class="pill c3 r2">serum</span>
  </section>

  <section class="panel" style="top:661px;height:166px">
    <div class="panel-body"></div>
    <h3 class="panel-tab" style="width:467px">color cosmetics products</h3>
    <span class="pill c1 r1">eyeliner</span>
    <span class="pill c2 r1">mascara</span>
    <span class="pill c3 r1">foundation</span>
    <span class="pill wide c1 r2">mineral make-up powder</span>
  </section>

  <section class="panel" style="top:841px;height:166px">
    <div class="panel-body"></div>
    <h3 class="panel-tab" style="width:505px">manicure/pedicure products</h3>
    <span class="pill c1 r1">cuticle oil</span>
    <span class="pill wide c2 r1">sugar &amp; salt scrub</span>
    <span class="pill wide c1 r2">foot soak/softener</span>
  </section>

  <section class="panel" style="top:1020px;height:168px">
    <div class="panel-body"></div>
    <h3 class="panel-tab" style="width:276px">spa products</h3>
    <span class="pill c1 r1">seaweed wrap</span>
    <span class="pill c2 r1">celulite cream</span>
    <span class="pill c3 r1">body mask</span>
    <span class="pill c1 r2">massage oils</span>
    <span class="pill c2 r2">candles</span>
  </section>
</div>
</body>
</html>
```